Brazilian-Italian food blogger looks for a yummy design for her blog

Ciao everyone! I am looking for a brand new design for my Wordpress food blog, MaRuPAN (marupan.net). The blog is about my deep love with food and with Bologna. I write particularly for the Brazilian crowd.
I talk about gastronomic curiosities of the town, delicious places and specialties that one can only find here. There are also many posts about my trips around Italy.
I would like the new design to be more sophisticated (or should I say professional?), but friendly at the same time.
If possible, I would like to keep its background very clean (if there are patters related to food, like the way it is now, even better), especially because I post many big colourful photos...
Also, since it is a personal blog, I would love if visitors could see a picture of mine and with a short description right at the homepage.
Thank you so much in advance.
Cheers,
Teresa.

Target Market(s)

Brazilian people interested in Italian culture and gastronomy.

Colors
fcca95

Requirements
Must have
• A neutral background that does not interfere with photos.
• My photo with a short description on the homepage.
Nice to have
• A background that has something to do with food.
Should not have
• It should not look like a girly blog.

```html
<!DOCTYPE html>
<html lang="en">
<head>
<meta charset="utf-8">
<title>MaRuPAN – Food Blog</title>
<link rel="stylesheet" href="https://fonts.googleapis.com/css2?family=Josefin+Sans:wght@400;600&family=Open+Sans:wght@400;600&display=swap">
<style>
  :root {
    --peach: #fcca95;
    --peach-deep: #f3b16e;
    --peach-bg: #f8dcb8;
    --orange: #d9823a;
    --red: #e8454b;
    --ink: #4a4a4a;
    --muted: #7a7a7a;
    --line: #e2e2e2;
    --white: #ffffff;
    --grey-btn: #9a9a9a;
  }
  * { box-sizing: border-box; margin: 0; padding: 0; }
  html, body { width: 680px; height: 1200px; overflow: hidden; }
  body {
    position: relative;
    font-family: "Open Sans", sans-serif;
    color: var(--ink);
    background: var(--peach-bg);
  }
  .food-pattern {
    position: absolute; inset: 0;
    background: linear-gradient(135deg, #f9e3c4 0%, #f5d3a8 50%, #f9e3c4 100%);
  }
  .page {
    position: absolute; left: 99px; top: 0; width: 498px; height: 1200px;
    background: var(--white);
  }
  .abs { position: absolute; }

  .logo {
    left: 35px; top: 24px;
    font-family: "Josefin Sans", sans-serif; font-weight: 600;
    font-size: 19px; color: var(--orange);
  }
  .search {
    left: 354px; top: 26px; width: 124px; height: 17px;
    border: 1px solid #cfcfcf; font-size: 7px; color: var(--muted);
    padding: 3px 6px; display: flex; justify-content: space-between; align-items: center;
  }
  .nav {
    left: 24px; top: 57px; width: 451px; height: 28px;
    background: var(--peach); display: flex; align-items: center;
    padding: 0 4px;
  }
  .nav a {
    font-size: 8px; color: var(--white); text-decoration: none;
    padding: 0 8px; line-height: 28px; white-space: nowrap;
  }
  .nav a.active { background: var(--peach-deep); }

  .hero-art {
    left: 148px; top: 100px; width: 172px; height: 192px;
    background: linear-gradient(90deg, #f2b07a 0%, #f6d48a 50%, #c9dca0 100%);
  }
  .slide-arrow {
    top: 178px; width: 21px; height: 21px; border-radius: 50%;
    background: #d9914a; display: flex; align-items: center; justify-content: center;
  }
  .banner-title {
    left: 115px; top: 228px; width: 270px; height: 27px;
    background: var(--peach); text-align: center;
    font-family: "Josefin Sans", sans-serif; font-size: 14px; line-height: 30px; color: #3b3b3b;
  }
  .banner-btn {
    left: 197px; top: 265px; width: 111px; height: 21px;
    background: var(--grey-btn); color: var(--white); text-align: center;
    font-size: 8px; line-height: 21px;
  }

  .post {
    left: 16px; width: 286px; height: 241px;
    border: 1px solid var(--line); box-shadow: 0 0 3px rgba(0,0,0,.06);
  }
  .post-title {
    position: absolute; left: 7px; top: 17px; width: 266px;
    font-family: "Josefin Sans", sans-serif; font-weight: 600; font-size: 9.6px;
    color: var(--orange); white-space: nowrap;
  }
  .post-photo { position: absolute; left: 7px; top: 38px; width: 263px; height: 104px; }
  .post-text {
    position: absolute; left: 7px; top: 156px; width: 266px;
    font-size: 5.8px; line-height: 12.5px; color: var(--muted);
  }
  .post-meta {
    position: absolute; left: 7px; top: 207px; width: 263px; height: 17px;
    border-top: 1px solid var(--line); border-bottom: 2px solid #333;
    display: flex; align-items: center; font-size: 6px; color: var(--muted); padding: 0 10px;
  }
  .post-meta span { margin-right: 16px; display: flex; align-items: center; gap: 3px; }
  .post-meta .date { margin: 0 0 0 auto; }

  .widget {
    left: 332px; width: 155px;
    border: 1px solid var(--line); box-shadow: 0 0 3px rgba(0,0,0,.06);
  }
  .widget-title {
    font-family: "Josefin Sans", sans-serif; font-weight: 400; font-size: 11px; color: var(--orange);
    text-align: center; margin-top: 14px;
  }
  .about-photo {
    width: 76px; height: 76px; border-radius: 50%; margin: 12px auto 0;
    background: radial-gradient(circle, #d8a77e 0%, #8a5d3b 100%);
  }
  .about-text {
    font-size: 6px; line-height: 12px; text-align: center; color: var(--muted);
    margin: 12px 16px 0;
  }
  .fan-head { display: flex; gap: 8px; padding: 10px 12px 0; }
  .fan-name { font-family: "Josefin Sans", sans-serif; font-weight: 600; font-size: 10px; color: var(--orange); margin-top: 9px; }
  .fan-small { font-size: 6px; }
  .like-btn {
    display: inline-block; margin-top: 3px; font-size: 5.5px; padding: 1px 4px;
    border: 1px solid #c7cfe0; background: #eef1f7; color: #3b5998;
  }
  .fan-count { font-size: 6px; font-weight: 600; padding: 6px 12px 4px; }
  .fan-grid { display: grid; grid-template-columns: repeat(6, 16px); gap: 4px; padding: 0 12px; }
  .fan-grid i { width: 16px; height: 16px; background: #c9b8a6; display: block; }
  .fan-grid i:nth-child(3n) { background: #b29a86; }
  .fan-grid i:nth-child(4n) { background: #d7c7b5; }
  .fan-foot { font-size: 5.5px; padding: 7px 12px; display: flex; align-items: center; gap: 3px; }
  .fan-foot b { width: 6px; height: 6px; background: #3b5998; display: inline-block; }

  .latest-title {
    font-family: "Josefin Sans", sans-serif; font-weight: 400; font-size: 12px; color: var(--red);
    margin: 15px 0 0 8px;
  }
  .latest-item { display: flex; gap: 8px; margin: 10px 0 0 9px; }
  .latest-thumb { width: 46px; height: 31px; background: linear-gradient(180deg, #9fb4c7 0%, #b7794c 60%, #8a5a3a 100%); flex: none; }
  .latest-copy { width: 84px; }
  .latest-item h4 { font-weight: 400; font-size: 7.5px; color: var(--red); white-space: nowrap; }
  .latest-item p { font-size: 6px; line-height: 9px; color: var(--muted); margin-top: 2px; }

  .archives { left: 332px; top: 884px; width: 155px; }
  .archives h3 { font-family: "Josefin Sans", sans-serif; font-weight: 400; font-size: 10.5px; color: var(--orange); }
  .archives ul { list-style: none; margin-top: 8px; }
  .archives li { font-size: 7px; color: var(--muted); height: 17.7px; display: flex; align-items: center; gap: 10px; }
  .archives li::before { content: "›"; font-size: 9px; color: #999; }

  .pager { left: 199px; top: 1102px; display: flex; gap: 1px; }
  .pager i { width: 8px; height: 8px; border: 1px solid #bbb; background: #eee; display: block; }
  .pager i.on { background: #777; border-color: #777; }
  .pager i.gap { border: 0; background: none; width: 6px; }

  .footer-line { left: 19px; top: 1138px; width: 460px; border-top: 1px solid #ddd; }
  .footer-links { left: 20px; top: 1155px; font-size: 7px; color: #333; }
  .footer-copy { left: 20px; top: 1172px; font-size: 7px; color: #333; }
  .social { left: 341px; top: 1161px; display: flex; gap: 6px; }
  .social i { width: 17px; height: 17px; display: block; }
</style>
</head>
<body>
  <div class="food-pattern" role="img" aria-label="Background pattern of illustrated chillies, cheese wedges, mushrooms and basil leaves"></div>

  <main class="page">
    <header>
      <div class="abs logo">MaRuPAN</div>
      <div class="abs search"><span>Search..</span>
        <svg width="7" height="7" viewBox="0 0 10 10"><circle cx="4" cy="4" r="3" fill="none" stroke="#888" stroke-width="1.4"/><line x1="6.3" y1="6.3" x2="9" y2="9" stroke="#888" stroke-width="1.4"/></svg>
      </div>
      <nav class="abs nav">
        <a class="active">HOME</a><a>I, TERE</a><a>THE BLOG</a><a>BELLA BO</a><a>CULINARY CONFESSIONS</a><a>BUONI POSTI</a><a>CONTACT</a>
      </nav>
    </header>

    <section class="hero">
      <div class="abs hero-art" role="img" aria-label="Illustration of fruits and vegetables arranged in a heart"></div>
      <div class="abs slide-arrow" style="left:24px"><svg width="8" height="10" viewBox="0 0 8 10"><path d="M6 1 2 5l4 4" fill="none" stroke="#fff" stroke-width="1.5"/></svg></div>
      <div class="abs slide-arrow" style="left:457px"><svg width="8" height="10" viewBox="0 0 8 10"><path d="M2 1l4 4-4 4" fill="none" stroke="#fff" stroke-width="1.5"/></svg></div>
      <div class="abs banner-title">MY DEEP LOVE WITH FOOD</div>
      <div class="abs banner-btn">OFFICIAL BLOG PAGE</div>
    </section>

    <article class="abs post" style="top:324px">
      <h2 class="post-title">QUISQUE SAGITTIS SEMPER FELIS, IN CONDIMENTUM</h2>
      <div class="post-photo" role="img" aria-label="Photo of a sushi platter" style="background:linear-gradient(90deg,#2c2a28,#c8643a 45%,#e9a070 65%,#3a3632)"></div>
      <p class="post-text">Duis autem vel eum iriure dolor in hendreritvulputate velit esse molestie consequat, vnll um dolore eu feugiat nulla facilisis at vero eros accumsan et iusto odio dignissim qui blan dipaesent luptatum zzril delenit augue duisolore te feugait nulla facilisi.</p>
      <div class="post-meta"><span>READ MORE</span><span>22 OCT</span><span>&#9679; 1</span><span>&#9829; 34</span><span class="date">15 April 2014</span></div>
    </article>

    <article class="abs post" style="top:584px">
      <h2 class="post-title">QUISQUE SAGITTIS SEMPER FELIS, IN CONDIMENTUM</h2>
      <div class="post-photo" role="img" aria-label="Photo of a seafood stew in a black pot" style="background:linear-gradient(90deg,#4a4c4e,#1e1e1e 30%,#d36a3a 60%,#e8a064 80%,#5a5d5f)"></div>
      <p class="post-text">Duis autem vel eum iriure dolor in hendreritvulputate velit esse molestie consequat, vnll um dolore eu feugiat nulla facilisis at vero eros accumsan et iusto odio dignissim qui blan dipaesent luptatum zzril delenit augue duisolore te feugait nulla facilisi.</p>
      <div class="post-meta"><span>READ MORE</span><span>22 OCT</span><span>&#9679; 1</span><span>&#9829; 34</span><span class="date">15 April 2014</span></div>
    </article>

    <article class="abs post" style="top:847px">
      <h2 class="post-title">QUISQUE SAGITTIS SEMPER FELIS, IN CONDIMENTUM</h2>
      <div class="post-photo" role="img" aria-label="Photo of pastry parcels topped with basil" style="background:linear-gradient(180deg,#8a1a1a,#e8dccb 35%,#f1e9dc 75%,#b8342a)"></div>
      <p class="post-text">Duis autem vel eum iriure dolor in hendreritvulputate velit esse molestie consequat, vnll um dolore eu feugiat nulla facilisis at vero eros accumsan et iusto odio dignissim qui blan dipaesent luptatum zzril delenit augue duisolore te feugait nulla facilisi.</p>
      <div class="post-meta"><span>READ MORE</span><span>22 OCT</span><span>&#9679; 1</span><span>&#9829; 34</span><span class="date">15 April 2014</span></div>
    </article>

    <aside>
      <section class="abs widget" style="top:324px;height:187px">
        <h3 class="widget-title">ABOUT ME</h3>
        <div class="about-photo" role="img" aria-label="Portrait photo of the blogger"></div>
        <p class="about-text">Claritas est etiam processus dynamicus, qui sequitur mutationem consuetudium lectorum. Mirum est notare quam littera gothica</p>
      </section>

      <section class="abs widget" style="top:528px;height:119px">
        <div class="fan-head">
          <div class="fan-name">MaRuPAN</div>
          <div class="fan-small" style="margin-top:4px">MaRuPAN<br><span class="like-btn">Like</span></div>
        </div>
        <div class="fan-count">30 people likes MaRuPAN</div>
        <div class="fan-grid" role="img" aria-label="Grid of follower profile photos">
          <i></i><i></i><i></i><i></i><i></i><i></i><i></i><i></i><i></i><i></i><i></i><i></i>
        </div>
        <div class="fan-foot"><b></b>Pagebook Plugin Login</div>
      </section>

      <section class="abs widget" style="top:670px;height:194px">
        <h3 class="latest-title">LATEST ARTICLES</h3>
        <div class="latest-item"><div class="latest-thumb" role="img" aria-label="Photo of Bologna rooftops"></div><div class="latest-copy"><h4>Nam liber tempouut</h4><p>Typi non habent claritatst m; est usius legentis qua.</p></div></div>
        <div class="latest-item"><div class="latest-thumb" role="img" aria-label="Photo of a Bologna street"></div><div class="latest-copy"><h4>Nam liber tempoumt</h4><p>Typi non habent claritatst m; est usius legentis qua.</p></div></div>
        <div class="latest-item"><div class="latest-thumb" role="img" aria-label="Photo of a square at dusk"></div><div class="latest-copy"><h4>Nam liber tempouiui</h4><p>Typi non habent claritatst m; est usius legentis qua.</p></div></div>
      </section>

      <section class="abs archives">
        <h3>ARCHIEVES</h3>
        <ul>
          <li>January 2013 (123)</li><li>February 2013</li><li>March 2013</li><li>April 2013</li>
          <li>May 2013</li><li>June 2013</li><li>July 2014</li><li>August 2014</li>
        </ul>
      </section>
    </aside>

    <div class="abs pager"><i class="on"></i><i></i><i></i><i></i><i></i><i></i><i></i><i></i><i></i><i class="gap"></i><i></i></div>

    <footer>
      <div class="abs footer-line"></div>
      <div class="abs footer-links">Terms and Conditions | Privacy Promise | FAQ's | Contact Us</div>
      <div class="abs footer-copy">Copyright © 2013. All Rights Reserved.</div>
      <div class="abs social">
        <i style="background:#3b5998"></i><i style="background:#2fa9e0"></i><i style="background:#f07a22"></i><i style="background:#d8302a"></i><i style="background:#8a5a44"></i>
      </div>
    </footer>
  </main>
</body>
</html>
```